Dentistry Office

We want a new design for a Dentist's office website.

The theme is: "We provide high quality, state-of-the-art, dental care in a comfortable, caring environment."

The site currently has a menu on the left of the page with about 40 items on it. There is a great deal of textual content on each page, plus several illustrations.

We want to do this using CSS, so we need specifications in the CSS for all possible elements. The CSS needs to be named in a logical manner for easy use.

Every dentist on the planet seems to use lots of Flash. We don't want to because it is so distracting. We are looking for an elegant solution targeting 24-55 age group, but not excluding anyone.

The following (from another dentist's site) can give you a taste of what we want to communicate on the site:

"After 20 years of teaching dentists how to refine their technique and many years of writing textbooks, I currently devote my time to my office and the hands-on practice of dentistry. I'd like to welcome you personally to my dental practice, and I invite you to meet my highly experienced team of professionals.

"We have offered complete dental care of the highest quality since 1978. We provide Preventive Services, Tooth Whitening and Cosmetic Dentistry for a beautiful smile, Endodontics (root canal treatment) to treat painful teeth, Sedation Dentistry so you can relax, and Dental Implants to restore what is missing. We offer total care.

"Our approach to your health is simple: We use our education, experience and dedication to provide every patient with superior dental care.

"This passion for excellence is not just a goal, but a standard every member of our team holds.

"We also pride ourselves with our state of the art procedures, training and technology. This includes creating a beautiful smile using techniques that preserve as much of the original tooth as possible.

"Our abilities are renowned throughout the dental profession and I hope if you have any questions you will contact us by an e-mail note, by phone or just by dropping by."

Keep in mind the screen shape and dimensions. Your design needs to work in the normal screen proportions, regardless of how it looks when you post it here. Scrolling is OK, but the first impression needs to work.
Updates

Keep in mind that there will be about 250 words, or more, on each page.

Competitors web sites:

http://www.brindlecovedentist.example/

http://www.brindlecovedentalcare.example/

http://www.grinsbymarlowvaledental.example/

http://www.tenbyfamilydentalcare.example/

http://www.quelmardental.example/

http://www.dovrinadental.example/

We need to compete with these.

Target Market(s)

Generally adults seeking the most experienced and comfortable-to-be-with dentist.

Industry/Entity Type

Training

Requirements
Must have
• Must stand apart from other dentists.
• Must be elegant.
• Must have a horizontal menu structure across all columns, NOT a vertical that requires scrolling, no popout, pop down, etc. menus.
• We are looking for something special.
• Do not waste your time or ours putting up templates and things you have used before.
• Personally, I do not see how someone outside the US can understand the northern California dental market. But you are welcome to try.
Should not have
• Flash or graphics that move
• The look of a template
• Folksy fonts
• Looks like you used it 20 times before

```html
<!DOCTYPE html>
<html lang="en">
<head>
<meta charset="utf-8">
<title>Larkmoor Dentist – Homepage Concepts</title>
<link href="https://fonts.googleapis.com/css2?family=Arimo:wght@400;700&display=swap" rel="stylesheet">
<style>
:root{
  --slate-900:#3c414c;
  --slate-800:#4a505c;
  --slate-700:#5b6270;
  --slate-500:#7d8492;
  --slate-300:#b9bec7;
  --mist:#e3e6ea;
  --mist-light:#eef0f3;
  --paper:#ffffff;
  --ink:#3a3a3a;
  --ink-soft:#5a5f69;
  --clock:#f0a323;
  --help:#2f74c6;
  --alert:#c7291f;
  --promo:#e7e1c9;
  --photo-skin:#d9b89c;
  --photo-warm:#c9a27e;
}
*{box-sizing:border-box;margin:0;padding:0}
html,body{width:907px;height:1200px;overflow:hidden;background:var(--paper)}
body{position:relative;font-family:"Arimo",Arial,sans-serif;color:var(--ink)}
ul{list-style:none}

.sheet{position:absolute;overflow:hidden;background:var(--paper)}
.sheet > *{position:absolute}
.concept-number{position:absolute;font-size:34px;font-weight:700;color:#222;line-height:1}

/* navigation tabs */
.tabs{display:flex;align-items:stretch;font-size:6.6px;font-weight:700;white-space:nowrap}
.tabs a{display:flex;align-items:center;padding:0 7px;color:inherit;text-decoration:none}
.tabs a.is-active{background:var(--paper);color:var(--slate-900)}
.tabs--dark{background:linear-gradient(var(--slate-700),var(--slate-900));color:#fff}
.tabs--light{background:linear-gradient(#f2f3f5,#d6d9de);color:var(--slate-900)}
.tabs--light a.is-active{box-shadow:0 0 0 1px var(--slate-300)}

/* mastheads */
.masthead--light{background:linear-gradient(90deg,#f6f7f8,#e1e5ea)}
.masthead--dark{background:linear-gradient(160deg,#5f6676 0%,#434957 55%,#5a6170 100%)}
.brand{position:absolute;font-weight:400;line-height:1.2;letter-spacing:.2px}
.brand--dark{color:var(--slate-700)}
.brand--light{color:#fff}
.call-line{position:absolute;font-size:7.5px;font-weight:400}
.photo{background:linear-gradient(135deg,var(--photo-skin),var(--photo-warm))}
.photo--family{background:linear-gradient(90deg,rgba(246,247,248,1) 0%,#e7dcd0 30%,#d8b79a 60%,#c69f7f 100%)}
.photo--portrait{background:radial-gradient(ellipse at 50% 40%,#e3c4a3 0%,#caa57f 35%,#5a6170 75%)}
.photo--house{background:linear-gradient(160deg,#8aa2b8 0%,#9aa57a 40%,#7a6a52 70%,#5f6f45 100%);border:1px solid var(--slate-300)}
.photo--light{background:linear-gradient(135deg,#cfd2d6 0%,#e89b3a 45%,#a9a9a9 100%);border:1px solid var(--slate-300)}

/* mega menu */
.mega{display:grid;grid-template-columns:repeat(5,1fr);background:var(--mist);border:1px solid var(--slate-300);font-size:5.6px;line-height:8.6px}
.mega h3{background:var(--slate-700);color:#fff;font-size:6px;font-weight:700;padding:1px 3px;line-height:9px;letter-spacing:.2px;white-space:nowrap}
.mega ul{padding:2px 3px}
.mega li{color:var(--ink);white-space:nowrap}
.mega li.is-current{background:var(--slate-700);color:#fff;padding-left:2px}

/* side menu */
.side-menu{font-size:5.6px;line-height:8.3px;background:var(--mist-light)}
.side-menu h3{background:linear-gradient(var(--slate-700),var(--slate-800));color:#fff;font-size:6px;font-weight:700;padding:1px 5px;line-height:9px;margin-top:2px}
.side-menu ul{padding:1px 0}
.side-menu li{padding-left:10px;position:relative;border-bottom:1px solid #fff;background:var(--mist);white-space:nowrap}
.side-menu li::before{content:"›";position:absolute;left:4px;color:var(--slate-700)}
.side-menu li.is-current{background:var(--slate-700);color:#fff}
.side-menu li.is-current::before{color:#fff}

/* content */
.section-title{font-size:7.6px;font-weight:700;color:var(--ink-soft)}
.body-copy{font-size:5.6px;line-height:7.4px;color:var(--ink)}
.pill-link{background:var(--slate-700);color:#fff;font-size:5px;padding:1px 6px;border-radius:2px;font-weight:700;white-space:nowrap}
.check-list{font-size:5.6px;line-height:10.4px;color:var(--ink)}
.check-list li{position:relative;padding-left:11px;white-space:nowrap}
.check-list li svg{position:absolute;left:0;top:2px;width:6px;height:6px}

.service-grid{display:grid;grid-template-columns:repeat(4,1fr)}
.service-card{background:var(--mist);border:1px solid var(--slate-300);font-size:5px;text-align:center;line-height:6px;color:var(--ink-soft);display:flex;flex-direction:column}
.service-card .photo{flex:1}
.service-card span{padding:1px 2px 2px}

.promo-box{background:linear-gradient(90deg,var(--promo),#f2eedf);border:1px solid var(--slate-300);border-radius:4px;overflow:hidden}
.promo-box p{position:absolute;color:var(--ink-soft)}
.promo-box .promo-note{background:var(--slate-700);color:#fff;font-size:4.8px;line-height:6px;padding:1px 5px;left:0;bottom:0;width:60%}
.promo-stack{text-align:center;color:var(--ink)}
.promo-stack .offer{font-size:7.4px;line-height:9px;font-weight:400}

.action{display:flex;align-items:center;justify-content:space-between;background:linear-gradient(var(--slate-500),var(--slate-700));color:#fff;font-size:7px;border-radius:3px;padding:0 4px 0 6px;height:15px}
.action svg{width:16px;height:16px;margin-right:-8px}
.action-note{font-size:5px;line-height:6.6px;color:var(--ink)}
.action-note b{font-weight:700}

.map{background:linear-gradient(135deg,#efeeea,#dcdcd6);border:1px solid var(--slate-300)}
.map-title{font-size:7px;font-weight:700;color:var(--ink-soft)}

.site-foot{background:linear-gradient(var(--slate-700),var(--slate-900));color:#fff;font-size:4.8px;line-height:8px}
.site-foot p{position:absolute;white-space:nowrap}
.top-tab{position:absolute;background:var(--paper);color:var(--ink-soft);font-size:5px;padding:1px 7px}
.phone-tab{background:linear-gradient(#f0f1f3,#d9dce0);color:var(--slate-900);font-size:8px;padding:3px 12px;clip-path:polygon(4% 0,96% 0,100% 100%,0 100%)}
</style>
</head>
<body>

<!-- Concept 1 -->
<section class="sheet" style="left:0;top:0;width:441px;height:618px" aria-label="Concept one">
  <header class="masthead--light" style="left:0;top:15px;width:441px;height:110px">
    <div class="photo photo--family" role="img" aria-label="Photo of a happy family" style="position:absolute;left:190px;top:0;width:251px;height:110px"></div>
    <h1 class="brand brand--dark" style="left:38px;top:24px;font-size:15px">Larkmoor Dentist<br>Henry Calder, DDS, FAGD</h1>
    <p class="call-line" style="left:42px;top:82px;color:var(--ink)">Call for Appointments: (555) 014-2290.</p>
  </header>
  <nav class="tabs tabs--dark" style="left:0;top:0;width:441px;height:15px;padding-left:38px">
    <a class="is-active">Home</a><a>Why we are differnt</a><a>Technologies we offer</a><a>Meet Dr.Calder</a><a>Our Staff</a><a>Contact Us</a><a>Links</a>
  </nav>
  <nav class="mega" style="left:36px;top:135px;width:370px;height:108px">
    <div><h3>EDUCATION</h3><ul><li>Emergency Dental Care</li><li class="is-current">Your Mouth</li><li>Your Tooth</li><li>Cracked Tooth?</li><li>Missing a Tooth?</li><li>Sensitive Teeth</li><li>Dry MouthTooth</li><li>GrindingSleep</li><li>Dentistry</li><li>Videos</li></ul></div>
    <div><h3>PREVENTATIVE</h3><ul><li>What is Preventive Care?</li><li>Taking Care of Your Teeth</li><li>Eating Right</li><li>Dental Check-Ups</li><li>Sealants</li><li>Periodontal Disease</li><li>Kicking the Habit</li><li>Night Guards</li><li>Dental X-Rays</li><li>Antibiotics with Treatment</li></ul></div>
    <div><h3>COSMETICS</h3><ul><li>Cosmetic Dentistry</li><li>Bleaching and Whitening</li><li>Cosmetic Bonding</li><li>Esthetic Veneers</li><li>Tooth Shaping</li></ul></div>
    <div><h3>RESTORATIONS</h3><ul><li>Crowns/Caps: Each Step</li><li>CMBRs</li><li>Porcelain Bridges</li><li>Bonded Dental Bridges</li><li>Gold Restorations</li><li>Implants</li><li>Treating CrackedTeeth</li><li>Periodontal (gum)</li><li>Treatment</li></ul></div>
    <div><h3>VISITING OUR OFFICE</h3><ul><li>Where to Stay</li><li>First Visit / Map</li><li>Financial Policy</li><li>Dental Insurance</li></ul></div>
  </nav>
  <h2 class="section-title" style="left:42px;top:257px">Welcome</h2>
  <p class="body-copy" style="left:42px;top:268px;width:264px">Lorem ipsum dolor sit amet, consectetuer adipiscing elit. Aenean commodo ligula eget dolor. Aenean massa. Cum sociis natoque penatibus et magnis dis parturient montes, nascetur ridiculus mus. Donec quam felis, ultricies nec, pellentesque eu, pretium quis, sem. Nulla consequat massa quis enim. Donec pede justo, fringilla vel, aliquet nec, vulputate eget, arcu. In enim justo, rhoncus ut, imperdiet a, venenatis vitae, justo massa quis enim. Donec pede justo, pretium quis, sem. Nulla consequat massa quis enim. Donec pede justo, fringilla vel. In enim justo, rhoncus ut, imperdiet a, venenatis vitae, justo massa quis enim. Donec pede justo, pretium quis, sem. Nulla consequat massa quis enim.</p>
  <div class="photo photo--house" role="img" aria-label="Photo of the dental office building" style="left:311px;top:268px;width:87px;height:65px"></div>
  <span class="pill-link" style="left:262px;top:326px">Learn more &gt;&gt;</span>
  <h2 class="section-title" style="left:44px;top:334px">Dr. Calder Provides</h2>
  <ul class="check-list" style="left:62px;top:352px">
    <li><svg viewBox="0 0 6 6"><path d="M0.5 3 L2.4 5 L5.5 0.8" fill="none" stroke="#3a3a3a" stroke-width="1.2"/></svg>General dentistry—oral hygiene, cavity detection and repair, crowns.</li>
    <li><svg viewBox="0 0 6 6"><path d="M0.5 3 L2.4 5 L5.5 0.8" fill="none" stroke="#3a3a3a" stroke-width="1.2"/></svg>Cosmetic/restorative dentistry—broken or misshapen teeth, crooked smiles, unsightly gaps</li>
    <li><svg viewBox="0 0 6 6"><path d="M0.5 3 L2.4 5 L5.5 0.8" fill="none" stroke="#3a3a3a" stroke-width="1.2"/></svg>Non-metal fillings—nontoxic, durable tooth-colored resin fillings that are proven to provide better results</li>
    <li><svg viewBox="0 0 6 6"><path d="M0.5 3 L2.4 5 L5.5 0.8" fill="none" stroke="#3a3a3a" stroke-width="1.2"/></svg>Tooth shaping—extending, shortening or otherwise reshaping teeth for improved esthetics</li>
    <li><svg viewBox="0 0 6 6"><path d="M0.5 3 L2.4 5 L5.5 0.8" fill="none" stroke="#3a3a3a" stroke-width="1.2"/></svg>Complete smile make-over's—resin veneers that reshape the whole mouth while preserving natural teeth</li>
    <li><svg viewBox="0 0 6 6"><path d="M0.5 3 L2.4 5 L5.5 0.8" fill="none" stroke="#3a3a3a" stroke-width="1.2"/></svg>Tooth whitening—at-home bleaching options to make teeth appear years younger</li>
    <li><svg viewBox="0 0 6 6"><path d="M0.5 3 L2.4 5 L5.5 0.8" fill="none" stroke="#3a3a3a" stroke-width="1.2"/></svg>Laser Dentistry, Sleep Dentistry, and Implant Dentistry with the Finest and Latest Equipment and Materials</li>
    <li><svg viewBox="0 0 6 6"><path d="M0.5 3 L2.4 5 L5.5 0.8" fill="none" stroke="#3a3a3a" stroke-width="1.2"/></svg>Dental Implants to replace missing teeth.</li>
    <li><svg viewBox="0 0 6 6"><path d="M0.5 3 L2.4 5 L5.5 0.8" fill="none" stroke="#3a3a3a" stroke-width="1.2"/></svg>Sedation Dentistry so you can be relaxed.</li>
  </ul>
  <div class="action" style="left:36px;top:471px;width:101px">Office Hours<svg viewBox="0 0 16 16"><circle cx="8" cy="8" r="7" fill="var(--clock)"/><circle cx="8" cy="8" r="5" fill="#fff"/><path d="M8 4.5V8H10.5" stroke="#555" stroke-width="1" fill="none"/></svg></div>
  <div class="action" style="left:36px;top:504px;width:101px">Where to stay?<svg viewBox="0 0 16 16"><circle cx="8" cy="8" r="7" fill="var(--help)"/><text x="8" y="11.5" text-anchor="middle" font-size="10" font-weight="700" fill="#fff" font-family="Arimo,Arial,sans-serif">?</text></svg></div>
  <div class="action" style="left:36px;top:537px;width:101px">Please call<svg viewBox="0 0 16 16"><path d="M3 5 C3 3 5 2 8 2 C11 2 13 3 13 5 L11 6.5 L10 5 L6 5 L5 6.5 Z M5 8 L11 8 L13 14 L3 14 Z" fill="var(--alert)"/></svg></div>
  <p class="action-note" style="left:38px;top:555px;width:100px">contact us outside office hours for an emergency, please call at <b>(555) 013-7741</b>.</p>
  <div class="promo-stack" style="left:146px;top:465px;width:130px">
    <p class="offer">We offer an Initial Patient<br>Examination X-rays and Cleaning</p>
  </div>
  <div class="photo photo--light" role="img" aria-label="Photo of a dental curing light" style="left:149px;top:494px;width:125px;height:51px"></div>
  <p style="left:171px;top:549px;font-size:11px">for $79.00.</p>
  <p style="left:237px;top:573px;font-size:5px">Learn More ››</p>
  <p class="map-title" style="left:285px;top:459px">Map to Office</p>
  <div class="map" role="img" aria-label="Street map to the office" style="left:283px;top:470px;width:121px;height:110px"></div>
  <footer class="site-foot" style="left:0;top:592px;width:441px;height:26px">
    <p style="left:42px;top:3px">Larkmoor Dentist • Tell A Friend • Privacy &amp; Legal • Dental Resources • New Patient Forms</p>
    <p style="left:42px;top:13px">Copyright © 2009. All Rights Reserved</p>
    <span class="top-tab" style="left:364px;top:3px">Top</span>
  </footer>
</section>

<!-- Concept 2 -->
<section class="sheet" style="left:463px;top:0;width:444px;height:618px" aria-label="Concept two">
  <header class="masthead--dark" style="left:0;top:0;width:444px;height:125px">
    <div class="photo photo--portrait" role="img" aria-label="Portrait photo of a smiling patient" style="position:absolute;left:245px;top:0;width:140px;height:125px"></div>
    <h1 class="brand brand--light" style="left:47px;top:36px;font-size:14px">Larkmoor Dentist<br>Henry Calder, DDS, FAGD</h1>
    <p class="call-line" style="left:47px;top:101px;color:#fff">Call for Appointments: (555) 014-2290.</p>
  </header>
  <nav class="tabs tabs--light" style="left:0;top:127px;width:444px;height:15px;padding-left:38px">
    <a class="is-active">Home</a><a>Why we are differnt</a><a>Technologies we offer</a><a>Meet Dr.Calder</a><a>Our Staff</a><a>Contact Us</a><a>Links</a>
  </nav>
  <nav class="side-menu" style="left:37px;top:155px;width:88px">
    <h3>EDUCATION</h3><ul><li class="is-current">Emergency Dental Care</li><li>Your Mouth</li><li>Your Tooth</li><li>Cracked Tooth?</li><li>Missing a Tooth?</li><li>Sensitive Teeth</li><li>Dry MouthTooth</li><li>GrindingSleep</li><li>Dentistry</li><li>Videos</li></ul>
    <h3>PREVENTATIVE</h3><ul><li>What is Preventive Care?</li><li>Taking Care of Your Teeth</li><li>Eating Right</li><li>Dental Check-Ups Sealants</li><li>Periodontal Disease</li><li>Kicking the Habit</li><li>Night Guards</li><li>Dental X-Rays</li><li>Antibiotics with Treatment</li></ul>
    <h3>COSMETICS</h3><ul><li>Cosmetic Dentistry</li><li>Bleaching and Whitening</li><li>Cosmetic Bonding</li><li>Esthetic Veneers</li><li>Tooth Shaping</li></ul>
    <h3>RESTORATIONS</h3><ul><li>Crowns/Caps: Each Step</li><li>CMBRs</li><li>Porcelain Bridges</li><li>Bonded Dental Bridges</li><li>Gold Restorations Implants</li><li>Treating CrackedTeeth</li><li>Periodontal (gum) Treatment</li></ul>
    <h3>VISITING OUR OFFICE</h3><ul><li>Where to Stay</li><li>First Visit / Map</li><li>Financial Policy</li><li>Dental Insurance</li></ul>
  </nav>
  <h2 class="section-title" style="left:137px;top:156px">Welcome</h2>
  <p class="body-copy" style="left:137px;top:169px;width:180px">Lorem ipsum dolor sit amet, consectetuer adipiscing elit. Aenean commodo ligula eget dolor. Aenean massa. Cum sociis natoque penatibus et magnis dis parturient montes, nascetur ridiculus mus. Donec quam felis, ultricies nec, pellentesque eu, pretium quis, sem. Nulla consequat massa quis enim. Donec pede justo, fringilla vel, aliquet nec, vulputate eget, arcu. In enim justo, rhoncus ut, imperdiet a, venenatis vitae, justo massa quis enim. Donec pede justo, pretium quis, sem. Nulla consequat massa quis enim.</p>
  <div class="photo photo--house" role="img" aria-label="Photo of the dental office building" style="left:321px;top:171px;width:86px;height:58px"></div>
  <span class="pill-link" style="left:271px;top:228px">Learn more &gt;&gt;</span>
  <h2 class="section-title" style="left:138px;top:242px">Dr. Calder Provides</h2>
  <div class="service-grid" style="left:139px;top:258px;width:270px;height:100px;column-gap:8px;row-gap:18px">
    <figure class="service-card"><div class="photo" role="img" aria-label="Photo of a smile"></div><span>General dentistry</span></figure>
    <figure class="service-card"><div class="photo" role="img" aria-label="Photo of restorative dental work"></div><span>Cosmetic/restorative dentistry</span></figure>
    <figure class="service-card"><div class="photo" role="img" aria-label="Photo of tooth-colored fillings" style="background:linear-gradient(135deg,#c4463e,#e7c9c0)"></div><span>Non-metal fillings</span></figure>
    <figure class="service-card"><div class="photo" role="img" aria-label="Photo of shaped teeth" style="background:linear-gradient(135deg,#f3e4e0,#d59a96)"></div><span>Tooth shaping</span></figure>
    <figure class="service-card"><div class="photo" role="img" aria-label="Photo of a smile make-over"></div><span>Complete smile make-over's</span></figure>
    <figure class="service-card"><div class="photo" role="img" aria-label="Photo of whitened teeth" style="background:linear-gradient(135deg,#b53a35,#efe7e4)"></div><span>Tooth whitening</span></figure>
    <figure class="service-card"><div class="photo" role="img" aria-label="Photo of a dental implant model" style="background:linear-gradient(135deg,#222,#9a9a9a)"></div><span>replace missing teeth</span></figure>
    <figure class="service-card"><div class="photo" role="img" aria-label="Photo of a dental laser" style="background:linear-gradient(135deg,#5a3fa0,#e89b3a)"></div><span>Laser Dentistry</span></figure>
  </div>
  <span class="pill-link" style="left:361px;top:364px">More &gt;&gt;</span>
  <div class="promo-box" style="left:140px;top:382px;width:267px;height:58px">
    <p style="left:9px;top:6px;font-size:7.6px;line-height:11px">We offer an Initial Patient<br>Examination X-rays and Cleaning</p>
    <p style="left:9px;top:30px;font-size:9px;font-weight:700;color:var(--ink)">for $79.00.</p>
    <p style="left:120px;top:36px;font-size:5px">Learn More ››</p>
    <div class="photo" role="img" aria-label="Photo of two smiling young people" style="position:absolute;left:178px;top:0;width:89px;height:58px;background:linear-gradient(135deg,#e7b1c5,#d8a57f)"></div>
    <p class="promo-note">New patients only. Offers are cash patients only.<br>Insurance will be billed at full value.</p>
  </div>
  <div class="action" style="left:140px;top:466px;width:102px">Office Hours<svg viewBox="0 0 16 16"><circle cx="8" cy="8" r="7" fill="var(--clock)"/><circle cx="8" cy="8" r="5" fill="#fff"/><path d="M8 4.5V8H10.5" stroke="#555" stroke-width="1" fill="none"/></svg></div>
  <div class="action" style="left:140px;top:499px;width:102px">Where to stay?<svg viewBox="0 0 16 16"><circle cx="8" cy="8" r="7" fill="var(--help)"/><text x="8" y="11.5" text-anchor="middle" font-size="10" font-weight="700" fill="#fff" font-family="Arimo,Arial,sans-serif">?</text></svg></div>
  <div class="action" style="left:140px;top:532px;width:102px">Please call<svg viewBox="0 0 16 16"><path d="M3 5 C3 3 5 2 8 2 C11 2 13 3 13 5 L11 6.5 L10 5 L6 5 L5 6.5 Z M5 8 L11 8 L13 14 L3 14 Z" fill="var(--alert)"/></svg></div>
  <p class="action-note" style="left:142px;top:550px;width:100px">contact us outside office hours for an emergency, please call at <b>(555) 013-7741</b>.</p>
  <p class="map-title" style="left:273px;top:455px">Map to Office</p>
  <div class="map" role="img" aria-label="Street map to the office" style="left:272px;top:466px;width:135px;height:112px"></div>
  <footer class="site-foot" style="left:0;top:585px;width:444px;height:33px">
    <p style="left:44px;top:4px">Larkmoor Dentist • Tell A Friend • Privacy &amp; Legal • Dental Resources • New Patient Forms</p>
    <p style="left:44px;top:16px">Copyright © 2009. All Rights Reserved</p>
    <span class="top-tab" style="left:366px;top:3px">Top</span>
  </footer>
</section>

<!-- Concept 4 -->
<section class="sheet" style="left:0;top:622px;width:453px;height:578px" aria-label="Concept four">
  <header class="masthead--dark" style="left:0;top:0;width:453px;height:126px">
    <div class="photo photo--portrait" role="img" aria-label="Portrait photo of a smiling patient" style="position:absolute;left:262px;top:0;width:150px;height:126px"></div>
    <h1 class="brand brand--light" style="left:48px;top:50px;font-size:15px">Larkmoor Dentist<br>Henry Calder, DDS, FAGD</h1>
  </header>
  <p class="phone-tab" style="left:38px;top:0;width:250px;height:18px">Call for Appointments: (555) 014-2290.</p>
  <nav class="tabs tabs--light" style="left:0;top:128px;width:453px;height:17px;padding-left:38px">
    <a class="is-active">Home</a><a>Why we are differnt</a><a>Technologies we offer</a><a>Meet Dr.Calder</a><a>Our Staff</a><a>Contact Us</a><a>Links</a>
  </nav>
  <nav class="side-menu" style="left:38px;top:158px;width:92px">
    <h3>EDUCATION</h3><ul><li>Emergency Dental Care</li><li class="is-current">Your Mouth</li><li>Your Tooth</li><li>Cracked Tooth?</li><li>Missing a Tooth?</li><li>Sensitive Teeth</li><li>Dry MouthTooth</li><li>GrindingSleep</li><li>Dentistry</li><li>Videos</li></ul>
    <h3>PREVENTATIVE</h3><ul><li>What is Preventive Care?</li><li>Taking Care of Your Teeth</li><li>Eating Right</li><li>Dental Check-Ups Sealants</li><li>Periodontal Disease</li><li>Kicking the Habit</li><li>Night Guards</li><li>Dental X-Rays</li><li>Antibiotics with Treatment</li></ul>
    <h3>COSMETICS</h3><ul><li>Cosmetic Dentistry</li><li>Bleaching and Whitening</li><li>Cosmetic Bonding</li><li>Esthetic Veneers</li><li>Tooth Shaping</li></ul>
    <h3>RESTORATIONS</h3><ul><li>Crowns/Caps: Each Step</li><li>CMBRs</li><li>Porcelain Bridges</li><li>Bonded Dental Bridges</li><li>Gold Restorations Implants</li><li>Treating CrackedTeeth</li><li>Periodontal (gum) Treatment</li></ul>
    <h3>VISITING OUR OFFICE</h3><ul><li>Where to Stay</li><li>First Visit / Map</li><li>Financial Policy</li><li>Dental Insurance</li></ul>
  </nav>
  <h2 class="section-title" style="left:143px;top:159px">Welcome</h2>
  <p class="body-copy" style="left:143px;top:172px;width:186px">Lorem ipsum dolor sit amet, consectetuer adipiscing elit. Aenean commodo ligula eget dolor. Aenean massa. Cum sociis natoque penatibus et magnis dis parturient montes, nascetur ridiculus mus. Donec quam felis, ultricies nec, pellentesque eu, pretium quis, sem. Nulla consequat massa quis enim. Donec pede justo, fringilla vel, aliquet nec, vulputate eget, arcu. In enim justo, rhoncus ut, imperdiet a, venenatis vitae, justo massa quis enim. Donec pede justo, pretium quis, sem. Nulla consequat massa quis enim. Donec pede justo, fringilla vel.</p>
  <div class="photo photo--house" role="img" aria-label="Photo of the dental office building" style="left:333px;top:174px;width:76px;height:62px"></div>
  <span class="pill-link" style="left:283px;top:232px">Learn more &gt;&gt;</span>
  <h2 class="section-title" style="left:143px;top:256px">Dr. Calder Provides</h2>
  <ul class="check-list" style="left:143px;top:270px;line-height:10.4px">
    <li><svg viewBox="0 0 6 6"><path d="M0.5 3 L2.4 5 L5.5 0.8" fill="none" stroke="#3a3a3a" stroke-width="1.2"/></svg>General dentistry—oral hygiene, cavity detection and repair, crowns.</li>
    <li><svg viewBox="0 0 6 6"><path d="M0.5 3 L2.4 5 L5.5 0.8" fill="none" stroke="#3a3a3a" stroke-width="1.2"/></svg>Cosmetic/restorative dentistry—broken or misshapen teeth, crooked smiles, unsightly gaps</li>
    <li><svg viewBox="0 0 6 6"><path d="M0.5 3 L2.4 5 L5.5 0.8" fill="none" stroke="#3a3a3a" stroke-width="1.2"/></svg>Non-metal fillings—nontoxic, durable tooth-colored resin fillings that are proven to provide better results</li>
    <li><svg viewBox="0 0 6 6"><path d="M0.5 3 L2.4 5 L5.5 0.8" fill="none" stroke="#3a3a3a" stroke-width="1.2"/></svg>Tooth shaping—extending, shortening or otherwise reshaping teeth for improved esthetics</li>
    <li><svg viewBox="0 0 6 6"><path d="M0.5 3 L2.4 5 L5.5 0.8" fill="none" stroke="#3a3a3a" stroke-width="1.2"/></svg>Complete smile make-over's—resin veneers that reshape the whole mouth while preserving natural teeth</li>
    <li><svg viewBox="0 0 6 6"><path d="M0.5 3 L2.4 5 L5.5 0.8" fill="none" stroke="#3a3a3a" stroke-width="1.2"/></svg>Tooth whitening—at-home bleaching options to make teeth appear years younger</li>
    <li><svg viewBox="0 0 6 6"><path d="M0.5 3 L2.4 5 L5.5 0.8" fill="none" stroke="#3a3a3a" stroke-width="1.2"/></svg>Laser Dentistry, Sleep Dentistry, and Implant Dentistry with the Finest and Latest Equipment and Materials</li>
    <li><svg viewBox="0 0 6 6"><path d="M0.5 3 L2.4 5 L5.5 0.8" fill="none" stroke="#3a3a3a" stroke-width="1.2"/></svg>Dental Implants to replace missing teeth.</li>
    <li><svg viewBox="0 0 6 6"><path d="M0.5 3 L2.4 5 L5.5 0.8" fill="none" stroke="#3a3a3a" stroke-width="1.2"/></svg>Sedation Dentistry so you can be relaxed.</li>
  </ul>
  <div class="promo-box" style="left:145px;top:367px;width:264px;height:72px">
    <p style="left:12px;top:7px;font-size:8.4px;line-height:12px">We offer an Initial Patient<br>Examination X-rays and Cleaning</p>
    <p style="left:12px;top:35px;font-size:12px;color:var(--ink)">for $79.00.</p>
    <p style="left:120px;top:41px;font-size:5px">Learn More ››</p>
    <div class="photo" role="img" aria-label="Photo of two smiling young people" style="position:absolute;left:168px;top:0;width:96px;height:72px;background:linear-gradient(135deg,#e7b1c5,#d8a57f)"></div>
    <p class="promo-note">New patients only. Offers are cash patients only.<br>Insurance will be billed at full value.</p>
  </div>
  <div class="action" style="left:146px;top:464px;width:106px">Office Hours<svg viewBox="0 0 16 16"><circle cx="8" cy="8" r="7" fill="var(--clock)"/><circle cx="8" cy="8" r="5" fill="#fff"/><path d="M8 4.5V8H10.5" stroke="#555" stroke-width="1" fill="none"/></svg></div>
  <div class="action" style="left:146px;top:497px;width:106px">Where to stay?<svg viewBox="0 0 16 16"><circle cx="8" cy="8" r="7" fill="var(--help)"/><text x="8" y="11.5" text-anchor="middle" font-size="10" font-weight="700" fill="#fff" font-family="Arimo,Arial,sans-serif">?</text></svg></div>
  <div class="action" style="left:146px;top:530px;width:106px">Please call<svg viewBox="0 0 16 16"><path d="M3 5 C3 3 5 2 8 2 C11 2 13 3 13 5 L11 6.5 L10 5 L6 5 L5 6.5 Z M5 8 L11 8 L13 14 L3 14 Z" fill="var(--alert)"/></svg></div>
  <p class="action-note" style="left:148px;top:548px;width:104px">contact us outside office hours for an emergency, please call at <b>(555) 013-7741</b>.</p>
  <p class="map-title" style="left:284px;top:452px">Map to Office</p>
  <div class="map" role="img" aria-label="Street map to the office" style="left:283px;top:463px;width:126px;height:102px"></div>
  <footer class="site-foot" style="left:0;top:568px;width:453px;height:10px">
    <p style="left:46px;top:1px">Larkmoor Dentist • Tell A Friend • Privacy &amp; Legal • Dental Resources • New Patient Forms</p>
    <span class="top-tab" style="left:380px;top:1px">Top</span>
  </footer>
</section>

<!-- Concept 3 -->
<section class="sheet" style="left:470px;top:622px;width:437px;height:578px" aria-label="Concept three">
  <header class="masthead--dark" style="left:0;top:0;width:437px;height:113px">
    <div class="photo photo--portrait" role="img" aria-label="Photo of a joyful patient with arms raised" style="position:absolute;left:232px;top:0;width:155px;height:113px"></div>
    <h1 class="brand brand--light" style="left:39px;top:35px;font-size:14px">Larkmoor Dentist<br>Henry Calder, DDS, FAGD</h1>
    <p class="call-line" style="left:39px;top:88px;color:#fff">Call for Appointments: (555) 014-2290.</p>
  </header>
  <nav class="tabs tabs--light" style="left:0;top:116px;width:437px;height:16px;padding-left:36px">
    <a class="is-active">Home</a><a>Why we are differnt</a><a>Technologies we offer</a><a>Meet Dr.Calder</a><a>Our Staff</a><a>Contact Us</a><a>Links</a>
  </nav>
  <nav class="mega" style="left:38px;top:140px;width:359px;height:102px">
    <div><h3>EDUCATION</h3><ul><li>Emergency Dental Care</li><li class="is-current">Your Mouth</li><li>Your Tooth</li><li>Cracked Tooth?</li><li>Missing a Tooth?</li><li>Sensitive Teeth</li><li>Dry MouthTooth</li><li>GrindingSleep</li><li>Dentistry</li><li>Videos</li></ul></div>
    <div><h3>PREVENTATIVE</h3><ul><li>What is Preventive Care?</li><li>Taking Care of Your Teeth</li><li>Eating Right</li><li>Dental Check-Ups</li><li>Sealants</li><li>Periodontal Disease</li><li>Kicking the Habit</li><li>Night Guards</li><li>Dental X-Rays</li><li>Antibiotics with Treatment</li></ul></div>
    <div><h3>COSMETICS</h3><ul><li>Cosmetic Dentistry</li><li>Bleaching and Whitening</li><li>Cosmetic Bonding</li><li>Esthetic Veneers</li><li>Tooth Shaping</li></ul></div>
    <div><h3>RESTORATIONS</h3><ul><li>Crowns/Caps: Each Step</li><li>CMBRs</li><li>Porcelain Bridges</li><li>Bonded Dental Bridges</li><li>Gold Restorations</li><li>Implants</li><li>Treating CrackedTeeth</li><li>Periodontal (gum)</li><li>Treatment</li></ul></div>
    <div><h3>VISITING OFFICE</h3><ul><li>Where to Stay</li><li>First Visit / Map</li><li>Financial Policy</li><li>Dental Insurance</li></ul></div>
  </nav>
  <h2 class="section-title" style="left:42px;top:250px">Welcome</h2>
  <p class="body-copy" style="left:42px;top:262px;width:258px">Lorem ipsum dolor sit amet, consectetuer adipiscing elit. Aenean commodo ligula eget dolor. Aenean massa. Cum sociis natoque penatibus et magnis dis parturient montes, nascetur ridiculus mus. Donec quam felis, ultricies nec, pellentesque eu, pretium quis, sem. Nulla consequat massa quis enim. Donec pede justo, fringilla vel, aliquet nec, vulputate eget, arcu. In enim justo, rhoncus ut, imperdiet a, venenatis vitae, justo massa quis enim. Donec pede justo, pretium quis, sem. Nulla consequat massa quis enim. Donec pede justo, fringilla vel.</p>
  <div class="photo photo--house" role="img" aria-label="Photo of the dental office building" style="left:305px;top:256px;width:82px;height:60px"></div>
  <span class="pill-link" style="left:256px;top:311px">Learn more &gt;&gt;</span>
  <h2 class="section-title" style="left:45px;top:322px">Dr. Calder Provides</h2>
  <div class="service-grid" style="left:57px;top:332px;width:322px;height:92px;column-gap:16px;row-gap:8px">
    <figure class="service-card"><div class="photo" role="img" aria-label="Photo of a smile"></div><span>General dentistry</span></figure>
    <figure class="service-card"><div class="photo" role="img" aria-label="Photo of restorative dental work"></div><span>Cosmetic/restorative dentistry</span></figure>
    <figure class="service-card"><div class="photo" role="img" aria-label="Photo of tooth-colored fillings" style="background:linear-gradient(135deg,#c4463e,#e7c9c0)"></div><span>Non-metal fillings</span></figure>
    <figure class="service-card"><div class="photo" role="img" aria-label="Photo of shaped teeth" style="background:linear-gradient(135deg,#f3e4e0,#d59a96)"></div><span>Tooth shaping</span></figure>
    <figure class="service-card"><div class="photo" role="img" aria-label="Photo of a smile make-over"></div><span>Complete smile make-over's</span></figure>
    <figure class="service-card"><div class="photo" role="img" aria-label="Photo of whitened teeth" style="background:linear-gradient(135deg,#b53a35,#efe7e4)"></div><span>Tooth whitening</span></figure>
    <figure class="service-card"><div class="photo" role="img" aria-label="Photo of a dental implant model" style="background:linear-gradient(135deg,#222,#9a9a9a)"></div><span>Replace missing teeth</span></figure>
    <figure class="service-card"><div class="photo" role="img" aria-label="Photo of a dental laser" style="background:linear-gradient(135deg,#5a3fa0,#e89b3a)"></div><span>Laser Dentistry</span></figure>
  </div>
  <div class="action" style="left:40px;top:451px;width:102px">Office Hours<svg viewBox="0 0 16 16"><circle cx="8" cy="8" r="7" fill="var(--clock)"/><circle cx="8" cy="8" r="5" fill="#fff"/><path d="M8 4.5V8H10.5" stroke="#555" stroke-width="1" fill="none"/></svg></div>
  <div class="action" style="left:40px;top:483px;width:102px">Where to stay?<svg viewBox="0 0 16 16"><circle cx="8" cy="8" r="7" fill="var(--help)"/><text x="8" y="11.5" text-anchor="middle" font-size="10" font-weight="700" fill="#fff" font-family="Arimo,Arial,sans-serif">?</text></svg></div>
  <div class="action" style="left:40px;top:515px;width:102px">Please call<svg viewBox="0 0 16 16"><path d="M3 5 C3 3 5 2 8 2 C11 2 13 3 13 5 L11 6.5 L10 5 L6 5 L5 6.5 Z M5 8 L11 8 L13 14 L3 14 Z" fill="var(--alert)"/></svg></div>
  <p class="action-note" style="left:42px;top:533px;width:100px">contact us outside office hours for an emergency, please call at <b>(555) 013-7741</b>.</p>
  <div class="promo-stack" style="left:142px;top:443px;width:134px">
    <p class="offer">We offer an Initial Patient<br>Examination X-rays and Cleaning</p>
  </div>
  <div class="photo photo--light" role="img" aria-label="Photo of a dental curing light" style="left:145px;top:470px;width:124px;height:50px"></div>
  <p style="left:165px;top:524px;font-size:11px">for $79.00.</p>
  <p style="left:232px;top:549px;font-size:5px">Learn More ››</p>
  <p class="map-title" style="left:278px;top:440px">Map to Office</p>
  <div class="map" role="img" aria-label="Street map to the office" style="left:278px;top:451px;width:119px;height:107px"></div>
  <footer class="site-foot" style="left:0;top:568px;width:437px;height:10px">
    <p style="left:44px;top:1px">Larkmoor Dentist • Tell A Friend • Privacy &amp; Legal • Dental Resources • New Patient Forms</p>
    <span class="top-tab" style="left:358px;top:1px">Top</span>
  </footer>
</section>

<span class="concept-number" style="left:8px;top:284px">1</span>
<span class="concept-number" style="left:475px;top:310px">2</span>
<span class="concept-number" style="left:482px;top:885px">3</span>
<span class="concept-number" style="left:11px;top:888px">4</span>

</body>
</html>
```